Business Card Design

I am an Event and Wedding Planner in need of an eye catching business card featuring my logo (attached), my contact details, and my company tagline (Making every celebration glow with wonder...) I would like the tagline in font similar the logo's font.
Updates
I have just noticed that my logo has a misspelling so for the final design, I will be uploading a corrected logo as soon as I have it.
My apologies.
Reason: Waiting on a corrected logo...Lantern is misspelled and it should say Weddings not Wedding
The logo has been corrected so now Lantern is spelled correctly and it says Weddings instead of Wedding. Please use Edwardian Script ITC as the font for the tagline so it will match the logo. Thank you for your patience.
Target Market(s)
Engaged couples and people hosting milestone celebrations. 25-50 years old, predominately female
Industry/Entity Type
Business
Contact Information for Business Card
Rosalind Merrow, Event Manager / Owner, Mobile: 0491 868 254, Email: rosalind@velvetlanternco.com.au, www.velvetlanternco.com.au, Making every celebration glow with wonder...

```html
<!DOCTYPE html>
<html lang="en">
<head>
<meta charset="utf-8">
<title>Velvet Lantern – Business Card</title>
<link rel="stylesheet" href="https://fonts.googleapis.com/css2?family=Cormorant+Garamond:wght@500;600&family=Pinyon+Script&display=swap">
<style>
  :root {
    --backdrop: #2a2a2c;
    --card: #fbf9f8;
    --card-back: #f1eeed;
    --crimson: #b0232e;
    --scarlet: #e2202a;
    --bloom-soft: rgba(200, 54, 47, 0.18);
    --bloom-mid: rgba(200, 54, 47, 0.35);
    --ink: #1d1b1b;
    --ink-soft: #3b3636;
    --paper-white: #ffffff;
  }
  * { box-sizing: border-box; margin: 0; padding: 0; }
  html, body { width: 1200px; height: 900px; overflow: hidden; }
  body {
    background: var(--backdrop);
    display: flex;
    flex-direction: column;
    align-items: center;
    justify-content: center;
    gap: 40px;
    font-family: "Cormorant Garamond", Georgia, serif;
    color: var(--ink);
  }
  .card {
    position: relative;
    width: 700px;
    height: 400px;
    background: var(--card);
    overflow: hidden;
    box-shadow: 0 10px 30px rgba(0,0,0,0.45);
  }
  .card--back { background: var(--card-back); }

  /* Front */
  .front-panel { position: absolute; inset: 0; width: 700px; height: 400px; }
  .brand { display: flex; align-items: center; gap: 10px; font-weight: 600; white-space: nowrap; }
  .brand-dot { width: 9px; height: 9px; border-radius: 50%; background: currentColor; flex: none; }
  .front-brand {
    position: absolute; left: 40px; top: 92px;
    color: var(--paper-white); font-size: 30px;
  }
  .front-web {
    position: absolute; left: 40px; top: 150px;
    color: var(--paper-white); font-size: 15px; font-weight: 500; letter-spacing: 0.3px;
  }
  .contact { position: absolute; left: 372px; top: 56px; width: 200px; }
  .contact-name { font-size: 28px; font-weight: 600; line-height: 1; white-space: nowrap; }
  .contact-role { font-size: 12px; font-weight: 500; text-align: right; margin-top: 3px; }
  .contact-phone { font-size: 30px; font-weight: 500; letter-spacing: 1px; margin-top: 2px; white-space: nowrap; }
  .tagline {
    font-family: "Pinyon Script", "Brush Script MT", cursive;
    color: var(--ink-soft); line-height: 1.3;
  }
  .front-tagline { position: absolute; left: 372px; top: 248px; width: 200px; font-size: 19px; }
  .floral-front {
    position: absolute; right: 0; top: 50px; width: 100px; height: 320px;
    background: linear-gradient(160deg, var(--bloom-soft), var(--bloom-mid) 50%, var(--bloom-soft));
    border-radius: 50px 0 0 50px;
  }

  /* Back */
  .back-tagline { position: absolute; left: 40px; top: 34px; width: 270px; font-size: 21px; }
  .floral-back-top {
    position: absolute; right: 0; top: 40px; width: 350px; height: 165px;
    background: linear-gradient(200deg, rgba(200,54,47,0.38), var(--bloom-soft) 70%, rgba(200,54,47,0));
    border-radius: 80px 0 0 130px;
  }
  .floral-back-left {
    position: absolute; left: 0; top: 150px; width: 260px; height: 150px;
    background: radial-gradient(ellipse at 40% 60%, rgba(130,36,32,0.32), rgba(130,36,32,0) 72%);
  }
  .back-brand {
    position: absolute; left: 330px; top: 228px;
    color: var(--ink); font-size: 42px;
  }
  .back-rule {
    position: absolute; left: 330px; top: 288px; width: 260px; height: 1px; background: var(--ink-soft);
  }
  .back-email {
    position: absolute; left: 330px; top: 300px;
    font-size: 17px; font-weight: 500;
  }
  .back-band {
    position: absolute; left: 0; bottom: 0; width: 100%; height: 26px; background: var(--scarlet);
  }
</style>
</head>
<body>
  <section class="card card--front">
    <svg class="front-panel" viewBox="0 0 700 400" aria-hidden="true">
      <path d="M0 0 H360 Q300 260 210 400 H0 Z" fill="var(--crimson)"/>
    </svg>
    <div class="brand front-brand"><span class="brand-dot"></span>Velvet Lantern</div>
    <div class="front-web">www.velvetlanternco.com.au</div>
    <div class="contact">
      <div class="contact-name">Rosalind Merrow</div>
      <div class="contact-role">Event Manager</div>
      <div class="contact-phone">0491 868 254</div>
    </div>
    <p class="tagline front-tagline">Making every celebration glow with wonder...</p>
    <div class="floral-front" role="img" aria-label="Red flowering vine ornament trailing down the right edge"></div>
  </section>

  <section class="card card--back">
    <div class="floral-back-top" role="img" aria-label="Red floral vine ornament across the upper right"></div>
    <div class="floral-back-left" role="img" aria-label="Dark red swirling leaf flourish on the left"></div>
    <p class="tagline back-tagline">Making every celebration glow with wonder...</p>
    <div class="brand back-brand"><span class="brand-dot"></span>Velvet Lantern</div>
    <div class="back-rule"></div>
    <div class="back-email">rosalind@velvetlanternco.com.au</div>
    <div class="back-band"></div>
  </section>
</body>
</html>
```